Corporate Design für Malermeister
Zielgruppe
Ich bin Malermeister ,
wir bieten komplettrenovierungen an vom Gestalten der Oberflächen, kreative Wandgestaltung Trockenbau, Bodenverlegearbeiten Parkett, Laminat, Teppich, designböden etc.
Fokus liegt bei den Malerarbeiten! Auch Fassaden werden restaurariert und gestaltet
Wir wollen modern und hochwertig rüber kommen
Aufgabenstellung
Das Logo soll zeigen, dass wir ein moderner kreativer Betrieb sind
da wir eine Diesntaleistung anbieten sollte es auch auf Vertrauen asutrahlen

```html
<!DOCTYPE html>
<html lang="de">
<head>
<meta charset="utf-8">
<title>KALMERO – Geschäftsausstattung</title>
<link href="https://fonts.googleapis.com/css2?family=Jost:wght@400;500;600;700&family=Tinos:ital,wght@0,400;0,700&family=Satisfy&display=swap" rel="stylesheet">
<style>
  :root{
    --paper:#fbfaf6;
    --ochre:#dea02a;
    --olive:#9c953a;
    --ink:#1f1f1f;
    --frame:#8a8a8a;
  }
  *{margin:0;padding:0;box-sizing:border-box}
  html,body{width:1200px;height:1200px;overflow:hidden}
  body{
    position:relative;
    background:linear-gradient(180deg,#fdfdfd 0%,#c9c9c9 30%,#a9a9a9 60%,#a2a29d 100%);
    font-family:'Jost',sans-serif;color:var(--ink);
  }
  .abs{position:absolute}
  .letter{left:117px;top:42px;width:789px;height:1116px;background:var(--paper);border:1px solid var(--frame)}
  .caps{text-transform:uppercase;font-family:'Jost',sans-serif;font-weight:500;white-space:nowrap}
  .brand-dot{border-radius:50%;background:var(--ochre)}
  .brand-name{font-family:'Jost',sans-serif;font-weight:700;color:var(--olive);letter-spacing:3px;line-height:1;white-space:nowrap}
  .tagline{font-size:15px;letter-spacing:5.2px;line-height:18px;color:#333;font-weight:400}
  .return-line{font-size:8.5px;letter-spacing:3px}
  .serif{font-family:'Tinos',serif;font-size:15.5px;line-height:19.1px;color:var(--ink)}
  .contact{font-size:9.8px;letter-spacing:3.6px;line-height:13.5px}
  .contact p + p{margin-top:7px}
  .fold-mark{width:5px;height:5px;border-radius:50%;background:var(--ochre)}
  .body-text{width:600px}
  .body-text p{margin-bottom:19px}
  .signature{font-family:'Satisfy',cursive;font-size:25px;color:#111;white-space:nowrap}
  .footer{width:789px;text-align:center;font-size:9.6px;letter-spacing:3.3px;line-height:14.6px}
  .card{width:384px;height:248px;border:1px solid var(--frame)}
  .card-front{left:730px;top:507px;background:var(--paper)}
  .card-back{left:730px;top:770px;background:var(--ochre);color:#fff}
  .card-back .caps{color:#fff}
</style>
</head>
<body>

<section class="abs letter" aria-label="Briefbogen">
  <div class="abs brand-dot" style="left:460px;top:101px;width:24px;height:24px"></div>
  <div class="abs brand-name" style="left:490px;top:97px;font-size:37px">KALMERO</div>
  <div class="abs caps tagline" style="left:567px;top:136px">Räume pflegen<br>Farbe wagen</div>

  <div class="abs caps return-line" style="left:94px;top:168px">Kalmero, Ahornweg 12, 34567 Feldingen</div>

  <div class="abs serif" style="left:94px;top:219px">
    Firmenname<br>Frau<br>Bettina Beispiel<br>Beispielstr. 133<br>76584 Beispieldorf
  </div>

  <div class="abs caps contact" style="left:479px;top:229px">
    <p>Kalmero<br>Ahornweg 12<br>34567 Feldingen</p>
    <p>Tel&nbsp; 01234 / 567890-12<br>Mobil&nbsp; 0170 / 123456789</p>
    <p>info@kalmero.de<br>kalmero.de</p>
  </div>

  <div class="abs fold-mark" style="left:35px;top:393px"></div>
  <div class="abs fold-mark" style="left:35px;top:556px"></div>
  <div class="abs fold-mark" style="left:35px;top:787px"></div>

  <div class="abs serif" style="left:470px;top:404px">Datum&nbsp; 3.Januar 2019</div>

  <div class="abs serif" style="left:94px;top:443px;font-weight:700">Angebot über Malerarbeiten</div>
  <div class="abs serif" style="left:94px;top:481px">Sehr geehrte Fau Beispiel,</div>

  <div class="abs serif body-text" style="left:94px;top:519px">
    <p>hiermit möchte ich Ihnen unser Angebot unterbreiten. Lorem ipsum dolor sit amet, consectetuer adipiscing elit. Aenean commodo ligula eget dolor. Aenean massa. Cum sociis natoque penatibus et magnis dis parturient montes, nascetur ridiculus mus. Donec quam felis, ultricies nec, pellentesque eu, pretium quis, sem. Nulla consequat massa quis enim. Donec pede justo, fringilla vel, aliquet nec, vulputate eget, arcu. In enim justo, rhoncus ut, imperdiet a, venenatis vitae, justo. Nullam dictum felis eu pede mollis pretium. Integer tincidunt. Cras dapibus. Vivamus elementum semper nisi.</p>
    <p>Lorem ipsum dolor sit amet, consectetuer adipiscing elit. Aenean commodo ligula eget dolor. Aenean massa. Cum sociis natoque penatibus et magnis dis parturient montes, nascetur ridiculus mus.</p>
    <p>Donec quam felis, ultricies nec, pellentesque eu, pretium quis, sem. Nulla consequat massa quis enim. Donec pede justo, fringilla vel, aliquet nec, vulputate eget, arcu. In enim justo, rhoncus ut, imperdiet a, venenatis vitae, justo. Nullam dictum felis eu pede mollis pretium. Integer tincidunt. Cras dapibus. Vivamus elementum semper nisi.</p>
  </div>

  <div class="abs serif" style="left:94px;top:862px">Mit freundlichen Grüßen</div>
  <div class="abs signature" style="left:94px;top:890px">Lukas Wendler</div>

  <div class="abs caps footer" style="left:0;top:1016px">
    Bankverbindung: Bankinstitut • IBAN DE00 1234 5678 9012 3456 78 • BIC&nbsp; BANKDEXX000<br>
    Inhaber: Lukas Wendler<br>
    Handelsregister: HRA 10000001 (Registergericht Berlin)<br>
    USt-IdNr: DE 000000000
  </div>
</section>

<section class="abs card card-front" aria-label="Visitenkarte Vorderseite">
  <div class="abs brand-dot" style="left:62px;top:92px;width:24px;height:24px"></div>
  <div class="abs brand-name" style="left:92px;top:88px;font-size:37px">KALMERO</div>
  <div class="abs caps tagline" style="left:164px;top:128px">Räume pflegen<br>Farbe wagen</div>
</section>

<section class="abs card card-back" aria-label="Visitenkarte Rückseite">
  <div class="abs brand-dot" style="left:150px;top:31px;width:16px;height:16px;background:#fff"></div>
  <div class="abs brand-name" style="left:172px;top:26px;font-size:23px;color:#fff;letter-spacing:2px">KALMERO</div>
  <div class="abs caps" style="left:33px;top:98px;font-size:14px;font-weight:700;letter-spacing:4.6px">Lukas Wendler</div>
  <div class="abs caps" style="left:33px;top:116px;font-size:10px;letter-spacing:3.6px">Malermeister</div>
  <div class="abs caps contact" style="left:165px;top:136px;color:#fff">
    <p>Ahornweg 12<br>34567 Feldingen</p>
    <p>Tel&nbsp; 01234 / 567890-12<br>Mobil&nbsp; 0170 / 123456789</p>
    <p>info@kalmero.de<br>kalmero.de</p>
  </div>
</section>

</body>
</html>
```